Telecommunications Company needs a business card design

We are looking for a sleek, professional and modern business card design based off our new logo. Will look at both light and dark options. On some designs please provide a small space for a QR code

Target Market(s)

B2B clients in Australia

Contact Information for Business Card

Name, Position, Brisbane (head) office, Phone number, email address, QR code (link to our website qlinetelecom.com.au

Colors
0054AA
0677BA
7BADD7
CADEEF
E8F1F8
0094D4
00A9DD
6FCCEA
C7EBF8
E9F6FB
00AB8E
00BBA5
67D7C9
C6EFE9
E9F9F6

```html
<!DOCTYPE html>
<html lang="en">
<head>
<meta charset="utf-8">
<title>Qline Telecom – Business Card</title>
<link rel="stylesheet" href="https://fonts.googleapis.com/css2?family=Open+Sans:wght@400;600;700&display=swap">
<style>
  :root {
    --backdrop: #2a2a2c;
    --card: #0b0b0c;
    --brand-blue: #0677BA;
    --brand-sky: #0094D4;
    --brand-teal: #00A9A0;
    --text-light: #e6e8ea;
    --text-muted: #9aa1a8;
    --divider: #2c2e30;
  }
  * { margin: 0; padding: 0; box-sizing: border-box; }
  html, body {
    width: 1200px; height: 900px; overflow: hidden;
    background: var(--backdrop);
    font-family: "Open Sans", sans-serif;
  }
  .stage {
    width: 1200px; height: 900px;
    display: flex; align-items: center; justify-content: center; gap: 40px;
  }
  .card {
    width: 540px; height: 309px;
    background: var(--card);
    box-shadow: 0 12px 30px rgba(0,0,0,0.55);
    position: relative;
  }
  .card-front { display: flex; }
  .brand-panel {
    width: 48%; display: flex; align-items: center; justify-content: center;
    border-right: 1px solid var(--divider);
  }
  .wordmark {
    display: flex; align-items: center; gap: 10px;
    font-weight: 700; color: var(--brand-sky);
    letter-spacing: 0.04em; text-transform: uppercase;
  }
  .wordmark-mark { width: 14px; height: 14px; background: var(--brand-sky); }
  .brand-panel .wordmark { font-size: 22px; }
  .contact-panel {
    flex: 1; padding: 62px 0 0 30px; color: var(--text-light);
  }
  .contact-name {
    font-size: 19px; font-weight: 600; color: var(--brand-sky);
    text-transform: uppercase; letter-spacing: 0.01em; line-height: 1.1;
  }
  .contact-role { font-size: 13px; margin-bottom: 14px; }
  .contact-list { list-style: none; font-size: 12px; line-height: 1.65; }
  .contact-list li { display: flex; align-items: center; gap: 8px; }
  .contact-list svg { width: 12px; height: 12px; flex: none; }
  .contact-list .accent { color: var(--brand-teal); }
  .contact-address { font-size: 12.5px; margin-top: 14px; line-height: 1.45; padding-left: 20px; }
  .card-back { display: flex; align-items: center; justify-content: center; }
  .card-back .wordmark { font-size: 28px; }
</style>
</head>
<body>
<main class="stage">
  <section class="card card-front" aria-label="Business card front">
    <div class="brand-panel">
      <div class="wordmark"><span class="wordmark-mark"></span>Qline Telecom</div>
    </div>
    <div class="contact-panel">
      <p class="contact-name">Daniel Hartley</p>
      <p class="contact-role">Managing Director</p>
      <ul class="contact-list">
        <li>
          <svg viewBox="0 0 24 24" fill="none" stroke="#0094D4" stroke-width="2.4"><path d="M5 3h4l2 5-3 2a12 12 0 0 0 6 6l2-3 5 2v4a2 2 0 0 1-2 2A17 17 0 0 1 3 5a2 2 0 0 1 2-2z"/></svg>
          044-987 654 321
        </li>
        <li>
          <svg viewBox="0 0 24 24" fill="none" stroke="#0094D4" stroke-width="2.4"><rect x="2" y="5" width="20" height="14"/><path d="M2 5l10 8 10-8"/></svg>
          info@qlinetelecom.com.au
        </li>
        <li>
          <svg viewBox="0 0 24 24" fill="none" stroke="#0094D4" stroke-width="2.2"><circle cx="12" cy="12" r="10"/><path d="M2 12h20M12 2c3 3 3 17 0 20M12 2c-3 3-3 17 0 20"/></svg>
          <span>www.<span class="accent">qlinetelecom</span>.com.au</span>
        </li>
      </ul>
      <p class="contact-address">218 Harbour Street<br>Eastfield, Brisbane</p>
    </div>
  </section>
  <section class="card card-back" aria-label="Business card back">
    <div class="wordmark"><span class="wordmark-mark"></span>Qline Telecom</div>
  </section>
</main>
</body>
</html>
```